Corporate Business Card

Very professional, Modern, Not to busy, include phone address email, website
(253) 617-4930, 18761 52nd Avenue S, Kent, WA 98047, martin@plumlinegroup.com, varkoworks.com

Target Market(s)

Manufacturing

Industry/Entity Type

Aero, machining, manufacturing, Off road racing

Contact Information for Business Card

Phone, address email, website

```html
<!DOCTYPE html>
<html lang="en">
<head>
<meta charset="utf-8">
<title>Varko Works — Business Card</title>
<link rel="stylesheet" href="https://fonts.googleapis.com/css2?family=Montserrat:wght@400;500;700&display=swap">
<style>
  :root {
    --navy: #17366f;
    --red: #d62b2f;
    --white: #ffffff;
    --ink: #1d1d1f;
    --silver: #c9ccd2;
    --bg-top: #f2f2f2;
    --bg-bottom: #3c3c3c;
  }
  * { margin: 0; padding: 0; box-sizing: border-box; }
  html, body { width: 1200px; height: 856px; overflow: hidden; }
  body {
    background: linear-gradient(180deg, var(--bg-top) 0%, #bdbdbd 50%, var(--bg-bottom) 100%);
    font-family: "Montserrat", Arial, sans-serif;
    display: flex;
    align-items: center;
    justify-content: center;
    gap: 50px;
  }
  .card {
    position: relative;
    width: 525px;
    height: 300px;
    box-shadow: 0 14px 30px rgba(0,0,0,0.35);
  }
  .card--front { background: var(--white); color: var(--ink); }
  .card--back { background: var(--navy); }

  .wordmark {
    position: absolute;
    display: flex;
    align-items: center;
    gap: 10px;
    font-weight: 700;
    letter-spacing: 0.02em;
    white-space: nowrap;
  }
  .wordmark__square { display: block; background: var(--red); }
  .card--front .wordmark { top: 62px; left: 222px; font-size: 34px; color: var(--navy); }
  .card--front .wordmark__square { width: 14px; height: 14px; }
  .card--back .wordmark { top: 108px; left: 120px; font-size: 50px; color: var(--silver); }
  .card--back .wordmark__square { width: 20px; height: 20px; background: var(--silver); }

  .rule { position: absolute; height: 2px; }
  .card--front .rule { top: 118px; left: 200px; width: 170px; background: var(--navy); }
  .card--back .rule { top: 188px; left: 90px; width: 230px; background: var(--silver); }

  .address {
    position: absolute;
    top: 150px;
    left: 34px;
    font-size: 13px;
    line-height: 1.45;
  }
  .contact {
    position: absolute;
    left: 34px;
    bottom: 26px;
    list-style: none;
    font-size: 13px;
    line-height: 1;
  }
  .contact__item { display: flex; align-items: center; gap: 9px; margin-top: 8px; }
  .contact__icon { width: 15px; height: 15px; flex: none; }
</style>
</head>
<body>
  <section class="card card--front" aria-label="Business card front">
    <div class="wordmark"><span class="wordmark__square"></span>Varko Works</div>
    <div class="rule"></div>

    <address class="address" style="font-style:normal">
      18761 52nd Avenue<br>
      S, Kent, WA 98047
    </address>

    <ul class="contact">
      <li class="contact__item">
        <svg class="contact__icon" viewBox="0 0 16 16" aria-hidden="true">
          <path fill="#d62b2f" d="M3.2 1.5 5.6 1l1.3 3.3-1.6 1.2a8 8 0 0 0 5.2 5.2l1.2-1.6 3.3 1.3-.5 2.4c-.2.8-1 1.3-1.8 1.2C6.8 13.4 2.6 9.2 2 3.3c-.1-.8.4-1.6 1.2-1.8z"/>
        </svg>
        (253) 617-4930
      </li>
      <li class="contact__item">
        <svg class="contact__icon" viewBox="0 0 16 16" aria-hidden="true">
          <rect x="1" y="3" width="14" height="10" rx="1" fill="#d62b2f"/>
          <path d="M1.5 3.8 8 9l6.5-5.2" fill="none" stroke="#fff" stroke-width="1.3"/>
        </svg>
        martin@plumlinegroup.com
      </li>
      <li class="contact__item">
        <svg class="contact__icon" viewBox="0 0 16 16" aria-hidden="true">
          <circle cx="8" cy="8" r="7" fill="#d62b2f"/>
          <ellipse cx="8" cy="8" rx="3" ry="7" fill="none" stroke="#fff" stroke-width="1"/>
          <path d="M1 8h14M2.5 4.5h11M2.5 11.5h11" stroke="#fff" stroke-width="1"/>
        </svg>
        www.varkoworks.com
      </li>
    </ul>
  </section>

  <section class="card card--back" aria-label="Business card back">
    <div class="wordmark"><span class="wordmark__square"></span>Varko Works</div>
    <div class="rule"></div>
  </section>
</body>
</html>
```